Civil Engineering Business Card Design

We need a business card design for an Civil Engineering Company located in Naples, Florida. The company name is Durvel Engineering.
What we do:
Site Evaluation
Review existing site conditions and zoning
Evaluation of potential development options
Evaluation of environmental permitting challenges
Prepare alternative master site development or redevelopment plan
Calculate cost and time lines for site development
Address political, environmental, social, and economic impacts of site development
Site Design
Prepare master site development plans
Zoning, rezoning, and zoning amendments for land use changes
Evaluate zoning and environmental permitting challenges
Value engineer alternative land development design and products
Residential Development
Plat development and design
Homeowner association document development
Single family development ranging from affordable housing to large estate projects
Multi family development ranging from duplexes to large scale condominiums
Amenity facilities such as golf courses, parks and clubhouse sites
Commercial Development
Office site and park designs development plans
Industrial site and park development plans
Shopping center site development design
Hospital site design development
Institutional Development
School design development and redevelopment plans
Park design development and enhancement plans
Downtown redevelopment plans for new and existing structures
Theater and park plan development
Parking garage design development
Governmental administration building design
Design Services
Site development
Environmental assessment
Roadway alignment and development
Surface water management
Drainage design
Water distribution system
Fire service analysis
Sewage collection systems
Sewage pump station and force main design
Cable utility conduit layout
Construction details
Construction documents
Technical specifications
Alternative methods and materials analysis
Services During Construction
Development of bid documents
Solicitation and processing of bids
Cost review and analysis
Construction cost estimating
Onsite construction observation
Coordination of field modifications to address unforeseen site conditions
Assess value engineering design and contract work
Review of pay requests and shop drawings
Review of warranties
Development assessment of onsite and offsite mitigation
Verification of construction completion, close out, and certification
Processing final pay requests and turn over
We want a clean design on a white background. We have a current logo but are not happy with it so changes would be greatly appreciated.
Industry/Entity Type
Construction
Contact Information for Business Card
Durvel Engineering
Creative Engineering Solutions Through Integrity and Experience
Marcus Pellow, President
4870 Brisket Ridge Road
Suite 517C
Naples, FL 34987
239-555-0164-Office, 239-555-0192-Mobile
Marcus@DurvelEng.example, www.DurvelEng.example

```html
<!DOCTYPE html>
<html lang="en">
<head>
<meta charset="utf-8">
<title>Durvel Engineering – Business Card</title>
<link rel="stylesheet" href="https://fonts.googleapis.com/css2?family=Roboto+Condensed:wght@400;700&display=swap">
<style>
  :root {
    --canvas: #d9d9db;
    --ink: #1c1c1c;
    --orange: #f7a823;
    --orange-deep: #f18f12;
    --white: #f5f5f5;
    --text-dark: #262626;
  }
  * { box-sizing: border-box; margin: 0; padding: 0; }
  html, body { width: 1200px; height: 988px; overflow: hidden; }
  body {
    background: var(--canvas);
    font-family: "Roboto Condensed", Arial, sans-serif;
    position: relative;
  }
  .card {
    position: absolute;
    left: 220px;
    width: 760px;
    height: 434px;
    overflow: hidden;
    box-shadow: 0 10px 24px rgba(0,0,0,.28);
  }
  .card-front { top: 40px; background: var(--ink); }
  .card-back { top: 514px; background: var(--white); }
  .card-shapes { position: absolute; inset: 0; width: 100%; height: 100%; }

  .brand {
    position: absolute;
    display: flex;
    align-items: center;
    gap: 12px;
  }
  .brand-mark {
    width: 34px; height: 34px;
    background: var(--orange);
    flex: none;
  }
  .brand-name {
    font-weight: 700;
    color: var(--orange);
    letter-spacing: .5px;
    white-space: nowrap;
  }
  .card-front .brand { left: 50%; top: 50%; transform: translate(-50%, -50%); }
  .card-front .brand-name { font-size: 46px; }

  .card-back .brand { right: 34px; bottom: 96px; }
  .card-back .brand-name { font-size: 30px; color: var(--orange-deep); }
  .card-back .brand-mark { width: 24px; height: 24px; background: var(--orange-deep); }

  .contact {
    position: absolute;
    left: 36px;
    top: 130px;
    color: var(--text-dark);
  }
  .person-name {
    font-size: 30px;
    font-weight: 700;
    letter-spacing: .5px;
    text-transform: uppercase;
  }
  .person-title {
    font-size: 13px;
    letter-spacing: 1.5px;
    text-transform: uppercase;
    margin-bottom: 18px;
  }
  .contact-list { list-style: none; }
  .contact-item {
    display: flex;
    align-items: center;
    gap: 10px;
    font-size: 14px;
    margin-bottom: 12px;
    white-space: nowrap;
  }
  .contact-icon { width: 22px; height: 22px; flex: none; }
</style>
</head>
<body>

<section class="card card-front" aria-label="Card front">
  <svg class="card-shapes" viewBox="0 0 760 434" preserveAspectRatio="none" aria-hidden="true">
    <polygon points="0,0 300,0 0,70" fill="var(--orange)"/>
    <polygon points="760,434 420,434 760,360" fill="var(--orange)"/>
  </svg>
  <div class="brand">
    <span class="brand-mark"></span>
    <span class="brand-name">Durvel Engineering</span>
  </div>
</section>

<section class="card card-back" aria-label="Card back">
  <svg class="card-shapes" viewBox="0 0 760 434" preserveAspectRatio="none" aria-hidden="true">
    <defs>
      <linearGradient id="orangeBand" x1="0" y1="0" x2="1" y2="1">
        <stop offset="0" stop-color="#f9b42d"/>
        <stop offset="1" stop-color="#f39a18"/>
      </linearGradient>
    </defs>
    <polygon points="0,0 440,0 380,434 0,434" fill="url(#orangeBand)"/>
    <polygon points="440,0 466,0 406,434 380,434" fill="var(--ink)"/>
  </svg>

  <div class="contact">
    <div class="person-name">Marcus Pellow</div>
    <div class="person-title">President</div>
    <ul class="contact-list">
      <li class="contact-item">
        <svg class="contact-icon" viewBox="0 0 22 22"><circle cx="11" cy="11" r="10" fill="none" stroke="#262626" stroke-width="1.5"/><path d="M7.5 6.5l2 0 1 2.5-1.3 1a6 6 0 0 0 2.8 2.8l1-1.3 2.5 1 0 2a1.2 1.2 0 0 1-1.3 1A8.5 8.5 0 0 1 6.5 7.8a1.2 1.2 0 0 1 1-1.3z" fill="#262626"/></svg>
        239-555-0164 Office
      </li>
      <li class="contact-item">
        <svg class="contact-icon" viewBox="0 0 22 22"><circle cx="11" cy="11" r="10" fill="none" stroke="#262626" stroke-width="1.5"/><rect x="8" y="5.5" width="6" height="11" rx="1" fill="#262626"/><rect x="9" y="7" width="4" height="7" fill="#f7a823"/></svg>
        239-555-0192 Mobile
      </li>
      <li class="contact-item">
        <svg class="contact-icon" viewBox="0 0 22 22"><circle cx="11" cy="11" r="10" fill="none" stroke="#262626" stroke-width="1.5"/><path d="M11 5a4 4 0 0 1 4 4c0 3-4 8-4 8s-4-5-4-8a4 4 0 0 1 4-4z" fill="#262626"/><circle cx="11" cy="9" r="1.5" fill="#f7a823"/></svg>
        4870 Brisket Ridge Road, Suite 517C, Naples, FL 34987
      </li>
      <li class="contact-item">
        <svg class="contact-icon" viewBox="0 0 22 22"><circle cx="11" cy="11" r="10" fill="none" stroke="#262626" stroke-width="1.5"/><rect x="5.5" y="7" width="11" height="8" fill="#262626"/><path d="M5.5 7l5.5 4.5 5.5-4.5" fill="none" stroke="#f7a823" stroke-width="1.2"/></svg>
        Marcus@DurvelEng.example
      </li>
      <li class="contact-item">
        <svg class="contact-icon" viewBox="0 0 22 22"><circle cx="11" cy="11" r="10" fill="none" stroke="#262626" stroke-width="1.5"/><circle cx="11" cy="11" r="5.5" fill="none" stroke="#262626" stroke-width="1.3"/><path d="M5.5 11h11M11 5.5c-2.5 3-2.5 8 0 11M11 5.5c2.5 3 2.5 8 0 11" fill="none" stroke="#262626" stroke-width="1"/></svg>
        www.DurvelEng.example
      </li>
    </ul>
  </div>

  <div class="brand">
    <span class="brand-mark"></span>
    <span class="brand-name">Durvel Engineering</span>
  </div>
</section>

</body>
</html>
```